4D Cradle Glimpse Luxury Ultrasound Billboard

Design a HIGH-END, MODERN billboard for my private prenatal ultrasound studio, 4D Cradle Glimpse, located in Pace, Florida.
This billboard will be viewed by drivers traveling at highway speeds, so it must be extremely clean, simple, and readable within 6 seconds.
About My Business
4D Cradle Glimpse is a private prenatal ultrasound studio specializing in:
Highest technology 4D/HD Ultrasounds
Early Gender Determination
Pregnancy Confirmation
I have been serving families for nearly 10 years and is known for creating a memorable experience, not just an ultrasound appointment.
Design Style
I DO NOT want:
Flowers
Leaves
Swirls
Glitter
Hearts everywhere
Busy backgrounds
Generic maternity stock graphics
I DO want:
Modern
Luxury
Upscale
Clean
Professional
Eye-catching
Premium medical spa feel
Colors
Use colors from my logo:
LOGO Green ( or a deep green)
Black
White
Soft Gold accents
Images:
Incorporate my professional headshot in a clean, modern way, logo, and the ultrasound images
Text
Keep wording minimal.
Primary Headline ( OPEN TO IDEAS) :
EXAMPLES ( WOULD RATHER SOMETHING MORE CATCHY)
" ADVANCED IMAGING. UNFORGETTABLE MOMENTS"
"MEET YOUR BABY BEFORE BIRTH"
Under headline:
4D Ultrasound • Early Gender • Pregnancy Confirmation
Business Name:
4D Cradle Glimpse
Private Prenatal Ultrasound Studio
Phone Number:
850-471-5923
Important
This billboard must be readable in 5–6 seconds from a moving vehicle.
Less text is better.
The phone number and business name must be visible from a distance.
The design should feel like a premium brand that immediately tells expecting parents:
“This is where I go to see my baby.”
Files Provided
Official logo
Headshot
Ultrasound images
Don’t make this look like a medical office billboard.
Make it look like a luxury baby experience billboard. That’s what separates 4D Cradle Glimpse from hospitals, OB offices, and all the new studios popping up around you. The emotional connection is what gets moms to book. ❤️
Billboard Size - 10.6” x 36”

```html
<!DOCTYPE html>
<html lang="en">
<head>
<meta charset="utf-8">
<title>4D Cradle Glimpse Billboard</title>
<link href="https://fonts.googleapis.com/css2?family=Libre+Baskerville:wght@700&family=Montserrat:wght@500;600;700&family=Roboto:wght@700&display=swap" rel="stylesheet">
<style>
  :root {
    --page-bg: #7a8189;
    --cream: #f6f2ec;
    --deep-green: #3e4f4a;
    --soft-gold: #b8893a;
    --scan-dark: #6e2c1c;
    --scan-light: #c98a6c;
    --portrait-light: #e6e3de;
    --portrait-mid: #d3cfc8;
    --white: #ffffff;
  }
  * { margin: 0; padding: 0; box-sizing: border-box; }
  html, body {
    width: 1145px; height: 1200px; overflow: hidden;
    background: var(--page-bg);
  }
  .billboard {
    position: absolute; left: 40px; top: 430px;
    width: 1065px; height: 340px;
    background: var(--cream);
    overflow: hidden;
    box-shadow: 0 6px 18px rgba(0,0,0,.35);
  }
  .scan-art { position: absolute; left: 0; top: 0; }
  .headshot {
    position: absolute; left: 840px; top: 0; width: 225px; height: 340px;
    background:
      linear-gradient(90deg, var(--cream) 0%, rgba(246,242,236,0) 22%),
      linear-gradient(180deg, var(--portrait-light) 0%, var(--portrait-mid) 100%);
  }
  .headline {
    position: absolute; left: 300px; width: 520px; text-align: center;
    font-family: "Libre Baskerville", serif; font-weight: 700;
    color: var(--deep-green); line-height: 1;
  }
  .headline--meet { top: 8px; font-size: 61px; letter-spacing: 1px; }
  .headline--baby { top: 57px; font-size: 88px; letter-spacing: 3px; }
  .subhead {
    position: absolute; left: 300px; width: 520px; top: 138px; text-align: center;
    font-family: "Montserrat", sans-serif; font-weight: 600; font-size: 34px;
    letter-spacing: 7px; color: var(--soft-gold); line-height: 1;
  }
  .divider { position: absolute; left: 370px; top: 172px; }
  .services {
    position: absolute; left: 337px; top: 194px; width: 443px; height: 27px;
    background: var(--deep-green); border-radius: 6px;
    display: flex; align-items: center; justify-content: center; gap: 14px;
    font-family: "Montserrat", sans-serif; font-weight: 500; font-size: 13.5px;
    color: var(--white);
  }
  .services li { list-style: none; display: flex; align-items: center; gap: 7px; }
  .services li::before {
    content: ""; width: 5px; height: 5px; border-radius: 50%; background: var(--soft-gold);
  }
  .brand {
    position: absolute; left: 330px; top: 228px; width: 197px; height: 87px;
    border: 2px solid var(--deep-green); border-radius: 9px;
    display: flex; flex-direction: column; align-items: center; justify-content: center; gap: 8px;
    font-family: "Montserrat", sans-serif; text-align: center;
  }
  .brand__name { font-weight: 700; font-size: 19px; color: var(--soft-gold); line-height: 1.05; }
  .brand__tag { font-weight: 600; font-size: 7.5px; letter-spacing: .6px; color: var(--deep-green); }
  .phone {
    position: absolute; left: 540px; top: 264px;
    display: flex; align-items: center; gap: 8px;
    font-family: "Roboto", sans-serif; font-weight: 700; font-size: 31px;
    color: var(--deep-green);
  }
</style>
</head>
<body>
  <main class="billboard">
    <svg class="scan-art" width="340" height="340" viewBox="0 0 340 340">
      <defs>
        <radialGradient id="scanTone" cx="45%" cy="45%" r="70%">
          <stop offset="0" stop-color="#c98a6c"/>
          <stop offset="1" stop-color="#6e2c1c"/>
        </radialGradient>
      </defs>
      <path role="img" aria-label="4D ultrasound image of twin babies face to face" d="M0 0 H265 Q392 170 251 340 H0 Z" fill="url(#scanTone)"/>
      <path d="M265 0 Q392 170 251 340" fill="none" stroke="#b8893a" stroke-width="4"/>
    </svg>

    <div class="headshot" role="img" aria-label="Portrait of the studio owner in green scrubs holding an ultrasound probe in her scanning room"></div>

    <h1 class="headline headline--meet">MEET YOUR</h1>
    <h1 class="headline headline--baby">BABY</h1>
    <p class="subhead">BEFORE BIRTH</p>

    <svg class="divider" width="380" height="22" viewBox="0 0 380 22">
      <line x1="5" y1="11" x2="170" y2="11" stroke="#b8893a" stroke-width="1"/>
      <line x1="207" y1="11" x2="378" y2="11" stroke="#b8893a" stroke-width="1"/>
      <path d="M188 19 L178 9 A5 5 0 0 1 188 4 A5 5 0 0 1 198 9 Z" fill="#b8893a"/>
    </svg>

    <ul class="services">
      <li>4D Ultrasound</li>
      <li>Early Gender</li>
      <li>Pregnancy Confirmation</li>
    </ul>

    <div class="brand">
      <span class="brand__name">4D Cradle Glimpse</span>
      <span class="brand__tag">PRENATAL ULTRASOUND STUDIO</span>
    </div>

    <div class="phone">
      <svg width="28" height="28" viewBox="0 0 28 28" aria-hidden="true">
        <circle cx="14" cy="14" r="12.5" fill="none" stroke="#b8893a" stroke-width="2"/>
        <path d="M9.5 8 l2.5-.6 1.5 3.2-1.6 1.2 a8 8 0 0 0 4 4 l1.2-1.6 3.2 1.5-.6 2.5 c-5.5.5-10.6-4.6-10.2-10.2z" fill="#b8893a"/>
      </svg>
      <span>850-471-5923</span>
    </div>
  </main>
</body>
</html>
```